Creation of an elegant and modern turnkey Shopify website

Hello,

We are a new company specializing in the sale of above-ground pools. We want to create a turnkey website, ideally using Shopify. For now, we need a "showcase" site, not an e-commerce platform, with four tabs:

Home Page (an overall presentation of the company)
Our Products (an overview of all the above-ground pools we sell)
Our Projects (a page inspired by Instagram to showcase photos of our future projects)
Contact (a page with all our contact information and a contact form)

We are looking to create a highly visual, elegant, and modern website with vibrant splashes of color. We will provide the text, photos (along with instructions on where to place them on each page), and all other necessary information as attachments.

Thank you in advance for your proposals!

The Brisa Lagoon Team

Target Market(s)

Targeted at Swiss customers (a translator will need to be installed for different languages)

Industry/Entity Type

Sale of customised above-ground pools

Coding

Coded - Design and coding required

Font styles to use
Sans Serif

Colors
0094D4
00A9DD
6FCCEA
C7EBF8
E9F6FB
00AB8E
00BBA5
67D7C9
C6EFE9
E9F9F6

Requirements
Must have
• A stunning, elegant and modern look
Nice to have
• Inspiration from the colors of our logo throughout the site, but in an elegant way
Should not have
• An overly classic look for swimming pool sites

```html
<!DOCTYPE html>
<html lang="en">
<head>
<meta charset="utf-8">
<title>Brisa Lagoon — Above-Ground Pools</title>
<link rel="stylesheet" href="https://fonts.googleapis.com/css2?family=Josefin+Sans:wght@300;400&family=Montserrat:wght@400;500&display=swap">
<style>
:root{
  --mint:#67D7C9;
  --mint-dark:#00BBA5;
  --sky:#6FCCEA;
  --ink:#111;
  --text:#333;
  --muted:#f4f4f4;
  --line:#e6e6e6;
  --white:#fff;
  --black:#000;
}
*{box-sizing:border-box;margin:0;padding:0}
html,body{width:1200px;height:3639px;overflow:hidden}
body{font-family:"Montserrat",sans-serif;color:var(--text);background:var(--white);position:relative}
.display{font-family:"Josefin Sans",sans-serif;font-weight:300;text-transform:uppercase;color:var(--ink)}
section,header,footer,.topbar{position:absolute;left:0;width:1200px}
.btn{display:inline-block;font-family:"Josefin Sans",sans-serif;text-transform:uppercase;font-size:15px;color:var(--ink);background:var(--mint);padding:14px 19px 11px;text-decoration:none}

.topbar{top:0;height:37px;background:var(--mint);font-size:12px;font-weight:500;color:var(--ink);text-align:center;line-height:37px}
.contact-bar{top:37px;height:52px;border-bottom:1px solid var(--line);font-size:12px;color:var(--ink)}
.contact-bar .item{position:absolute;top:17px;display:flex;align-items:center;gap:6px}
.search{position:absolute;left:758px;top:12px;width:327px;height:32px;background:var(--muted);font-size:11px;color:#888;padding:10px 18px}
.search svg{position:absolute;right:16px;top:11px}
.nav{top:89px;height:82px}
.brand{position:absolute;left:128px;top:20px;font-family:"Josefin Sans",sans-serif;font-weight:300;font-size:22px;line-height:22px;color:var(--mint-dark);letter-spacing:1px}
.menu{position:absolute;left:404px;top:33px;display:flex;gap:33px;font-size:14px;color:var(--ink)}
.tools{position:absolute;left:955px;top:32px;display:flex;gap:18px;align-items:center;font-size:15px;font-weight:500;color:var(--ink)}

.hero{top:171px;height:555px;background:linear-gradient(180deg,#b9c7cb 0%,#98b7bf 30%,#3b9fb3 55%,#5aaebd 62%,#8a6a50 75%,#6b4a35 100%);text-align:center}
.hero .welcome{position:absolute;top:140px;width:100%;font-size:24px;color:var(--mint)}
.hero h1{position:absolute;top:170px;width:100%;font-family:"Josefin Sans",sans-serif;font-weight:400;font-size:100px;color:var(--white);letter-spacing:1px}
.hero p{position:absolute;top:290px;width:100%;font-size:13px;line-height:22px;color:var(--white)}
.hero .btn{position:absolute;top:352px;left:510px;font-size:14px;padding:15px 24px 12px}

.intro{top:726px;height:357px;background:var(--muted);text-align:center}
.intro h2{position:absolute;top:70px;width:100%;font-size:38px;line-height:48px}
.intro .lead{position:absolute;top:178px;width:100%;font-size:14px;color:var(--mint-dark)}
.intro .body{position:absolute;top:214px;left:190px;width:820px;font-size:12.5px;line-height:25px;color:var(--ink)}

.why{top:1083px;height:573px;text-align:center}
.why h2{position:absolute;top:68px;width:100%;font-size:38px;line-height:43px}
.card{position:absolute;top:189px;width:316px}
.card .photo{height:193px;width:316px}
.card h3{margin-top:28px;font-family:"Josefin Sans",sans-serif;font-weight:400;font-size:17px;text-transform:uppercase;color:var(--ink)}
.card p{margin-top:8px;font-size:12px;line-height:20px;color:var(--ink);padding:0 32px}
.arrow{position:absolute;top:297px;width:22px;height:22px;border-radius:50%;background:#999;display:flex;align-items:center;justify-content:center}

.services{top:1656px;height:446px;background:var(--muted)}
.services .photo{position:absolute;left:0;top:0;width:600px;height:446px;background:radial-gradient(circle at 60% 40%,#cbeef3,#7fcedb 55%,#3fb2c2)}
.services h2{position:absolute;left:632px;top:98px;font-size:38px}
.services p{position:absolute;left:632px;top:160px;width:460px;font-size:12px;line-height:25px;color:var(--ink)}
.services .btn{position:absolute;left:630px;top:281px}

.satisfaction{top:2102px;height:379px;background:linear-gradient(160deg,#86d6ef,#6fcbe8 60%,#7ad0ea);text-align:center}
.satisfaction h2{position:absolute;top:78px;width:100%;font-size:38px}
.satisfaction p{position:absolute;top:142px;left:170px;width:860px;font-size:15px;line-height:30px;color:var(--ink)}
.satisfaction .btn{position:absolute;top:256px;left:513px;background:var(--white)}

.contact{top:2481px;height:545px}
.contact h2{position:absolute;left:110px;top:175px;font-size:38px}
.contact p{position:absolute;left:110px;top:228px;width:440px;font-size:12px;line-height:25px;color:var(--ink)}
.contact .btn{position:absolute;left:108px;top:351px}
.contact .photo{position:absolute;left:603px;top:80px;width:487px;height:382px;background:linear-gradient(160deg,#dfeeed 0%,#8ed7cc 50%,#3d9e92 100%)}

.dreams{top:3026px;height:200px;background:var(--muted);text-align:center}
.dreams h2{position:absolute;top:90px;width:100%;font-size:38px}
.dreams .art{position:absolute;left:335px;top:146px;width:770px;height:50px;background:linear-gradient(90deg,#ececec,#d8f1f3 65%,#e4e4e4)}

.site-footer{top:3226px;height:413px;background:var(--black);color:var(--white)}
.site-footer .logo{position:absolute;left:130px;top:80px;width:240px;font-family:"Josefin Sans",sans-serif;font-weight:300;font-size:50px;line-height:58px;color:var(--sky);text-align:center}
.socials{position:absolute;left:190px;top:258px;display:flex;gap:7px}
.socials span{width:18px;height:18px;border-radius:50%;background:var(--sky)}
.fcol{position:absolute;top:80px;font-size:14px;line-height:20px}
.fcol h4{font-family:"Josefin Sans",sans-serif;font-weight:400;font-size:18px;text-transform:uppercase;margin-bottom:22px}
.fcol ul{list-style:none}
.fcol li{margin-bottom:10px}
.info li{display:flex;gap:14px;margin-bottom:16px}
.info svg{flex:none;margin-top:3px}
.site-footer .rule{position:absolute;left:112px;top:315px;width:976px;height:1px;background:#222}
.copy{position:absolute;top:354px;width:100%;text-align:center;font-size:15px}
</style>
</head>
<body>

<div class="topbar">Free Shipping On Orders Over $200</div>

<header class="contact-bar">
  <div class="item" style="left:126px">
    <svg width="11" height="11" viewBox="0 0 24 24"><path d="M6.6 10.8a15 15 0 0 0 6.6 6.6l2.2-2.2c.3-.3.7-.4 1-.2 1.1.4 2.3.6 3.6.6.6 0 1 .4 1 1V20c0 .6-.4 1-1 1A17 17 0 0 1 3 4c0-.6.4-1 1-1h3.5c.6 0 1 .4 1 1 0 1.3.2 2.5.6 3.6.1.3 0 .7-.2 1z" fill="#111"/></svg>
    Call : 100-555-0142
  </div>
  <div class="item" style="left:312px">
    <svg width="13" height="11" viewBox="0 0 24 18"><rect x="1.5" y="1.5" width="21" height="15" fill="none" stroke="#111" stroke-width="2"/><path d="M2 2l10 8 10-8" fill="none" stroke="#111" stroke-width="2"/></svg>
    info@brisalagoon.com
  </div>
  <div class="search">Search
    <svg width="10" height="10" viewBox="0 0 24 24"><circle cx="10" cy="10" r="7" fill="none" stroke="#111" stroke-width="3"/><path d="M15 15l7 7" stroke="#111" stroke-width="3"/></svg>
  </div>
</header>

<header class="nav">
  <div class="brand">BRISA<br>LAGOON</div>
  <nav class="menu"><span>Home</span><span>Our Products</span><span>Our Projects</span><span>Contact Us</span></nav>
  <div class="tools">
    <svg width="14" height="15" viewBox="0 0 24 24"><circle cx="12" cy="7" r="5" fill="#111"/><path d="M2 23c0-6 4.5-9 10-9s10 3 10 9z" fill="#111"/></svg>
    <svg width="18" height="15" viewBox="0 0 24 20"><path d="M2 7h20l-3 12H5z" fill="none" stroke="#6FCCEA" stroke-width="2"/><path d="M7 7l5-6 5 6" fill="none" stroke="#6FCCEA" stroke-width="2"/></svg>
    <span style="display:flex;align-items:center;gap:4px;margin-left:14px">
      <svg width="14" height="14" viewBox="0 0 24 24"><circle cx="12" cy="12" r="10" fill="none" stroke="#111" stroke-width="2"/><ellipse cx="12" cy="12" rx="4" ry="10" fill="none" stroke="#111" stroke-width="2"/><path d="M2 12h20" stroke="#111" stroke-width="2"/></svg>
      En
      <svg width="8" height="6" viewBox="0 0 8 6"><path d="M0 0h8L4 5z" fill="#111"/></svg>
    </span>
  </div>
</header>

<section class="hero" role="img" aria-label="Poolside view from a wooden deck with a potted palm and blue water">
  <div class="welcome display">Welcome to</div>
  <h1>BRISA LAGOON</h1>
  <p>Lorem ipsum dolor sit amet, consectetur adipiscing elit, sed do eiusmod<br>tempor incididunt ut labore et dolore magna aliqua.</p>
  <a class="btn">Shop Now</a>
</section>

<section class="intro">
  <h2 class="display">Transform your garden with<br>our premium above-ground pools!</h2>
  <div class="lead">Achieve your dreams with our custom, tailor-made above-ground pools.</div>
  <p class="body">Imagine an exceptional relaxation and leisure space right in your own backyard. With our unparalleled expertise and commitment to excellence, we create above-ground pools that exceed all expectations. Our exclusive, custom-designed models are crafted to combine style, durability, and innovation, offering a unique and refined experience.</p>
</section>

<section class="why">
  <h2 class="display">Why choose our<br>above-ground pools?</h2>
  <div class="arrow" style="left:51px"><svg width="8" height="8" viewBox="0 0 8 8"><path d="M6 0L2 4l4 4" fill="none" stroke="#fff" stroke-width="1.5"/></svg></div>
  <div class="card" style="left:112px">
    <div class="photo" role="img" aria-label="White round above-ground pool on a paved terrace" style="background:linear-gradient(180deg,#a6cbe6 0%,#9fbf9a 45%,#e3eaee 75%)"></div>
    <h3>Superior Quality:</h3>
    <p>Each pool is constructed with high-quality materials, ensuring exceptional durability and strength.</p>
  </div>
  <div class="card" style="left:442px">
    <div class="photo" role="img" aria-label="Round blue pool set in a green garden beside a chalet" style="background:linear-gradient(180deg,#5d8a3e 0%,#3a9bd2 55%,#5f9a3c 100%)"></div>
    <h3>Elegant Design:</h3>
    <p>Our pools come in a variety of styles and finishes,seamlessly blending into any garden setting.</p>
  </div>
  <div class="card" style="left:773px">
    <div class="photo" role="img" aria-label="Wood-clad round pool on a lawn with sun loungers" style="background:linear-gradient(180deg,#4b95dc 0%,#4f8d2e 55%,#7a6a3a 100%)"></div>
    <h3>Custom and Tailor-made:</h3>
    <p>Create the pool of your dreams with our customization options, tailored to your specific tastes and needs.</p>
  </div>
  <div class="arrow" style="left:1129px"><svg width="8" height="8" viewBox="0 0 8 8"><path d="M2 0l4 4-4 4" fill="none" stroke="#fff" stroke-width="1.5"/></svg></div>
</section>

<section class="services">
  <div class="photo" role="img" aria-label="Person in a sun hat relaxing at the edge of turquoise pool water"></div>
  <h2 class="display">Personalized services</h2>
  <p>We understand that every garden and client is unique. That's why we offer personalized services, from design to installation and after-sales support. Our team of experts is here to answer all your questions and guide you throughout your project.</p>
  <a class="btn">Learn More</a>
</section>

<section class="satisfaction" role="img" aria-label="Soft underwater pool background in light blue">
  <h2 class="display">Guaranteed satisfaction</h2>
  <p>Your satisfaction is our top priority. We are committed to providing you with exceptional service and the highest quality products. Join our community of satisfied customers who are already enjoying their custom above-ground pools. 10-Year Warranty!</p>
  <a class="btn">Learn More</a>
</section>

<section class="contact">
  <h2 class="display">Contact us today</h2>
  <p>Don't wait any longer to transform your garden into a wellness oasis. Contact us today to discover our range of customizable above-ground pools and get a tailored quote. Dive into a world of infinite possibilities with [Your Company Name].</p>
  <a class="btn">Learn More</a>
  <div class="photo" role="img" aria-label="Striped teal and white beach cabin with folded parasols"></div>
</section>

<section class="dreams">
  <div class="art" role="img" aria-label="Line drawing of an above-ground pool and a lounge chair"></div>
  <h2 class="display">We bring your pool dreams to life!</h2>
</section>

<footer class="site-footer">
  <div class="logo">BRISA<br>LAGOON</div>
  <div class="socials"><span></span><span></span><span></span><span></span></div>
  <div class="fcol info" style="left:448px">
    <h4>Contact Information</h4>
    <ul>
      <li><svg width="12" height="14" viewBox="0 0 24 28"><path d="M12 0a10 10 0 0 0-10 10c0 7 10 18 10 18s10-11 10-18A10 10 0 0 0 12 0z" fill="#fff"/><circle cx="12" cy="10" r="4" fill="#000"/></svg><span>12b Brisa Lagoon dolor sit amet,<br>consectetur adipiscing elit,</span></li>
      <li><svg width="14" height="11" viewBox="0 0 24 18"><rect width="24" height="18" rx="2" fill="#fff"/><path d="M1 2l11 8 11-8" fill="none" stroke="#000" stroke-width="2"/></svg><span>info@brisalagoon.com</span></li>
      <li><svg width="13" height="13" viewBox="0 0 24 24"><path d="M6.6 10.8a15 15 0 0 0 6.6 6.6l2.2-2.2c.3-.3.7-.4 1-.2 1.1.4 2.3.6 3.6.6.6 0 1 .4 1 1V20c0 .6-.4 1-1 1A17 17 0 0 1 3 4c0-.6.4-1 1-1h3.5c.6 0 1 .4 1 1 0 1.3.2 2.5.6 3.6.1.3 0 .7-.2 1z" fill="#fff"/></svg><span>100-555-0142</span></li>
    </ul>
  </div>
  <div class="fcol" style="left:772px">
    <h4>Quick Links</h4>
    <ul><li>Home</li><li>Our Products</li><li>Our Projects</li><li>Contact Us</li></ul>
  </div>
  <div class="fcol" style="left:950px">
    <h4>Support</h4>
    <ul><li>Terms&amp;condtions</li><li>Privacy Policy</li><li>Terms of Use</li></ul>
  </div>
  <div class="rule"></div>
  <div class="copy">©Copyrights 2024 Brisa Lagoon. &nbsp;| &nbsp;&nbsp;All Rights Reserved</div>
</footer>

</body>
</html>
```